Rental Product Flyer

We have an outdated flyer that we give to prospective customers. The flyer describes the products we rent and has pictures or drawings. Would like to update with better pictures or maybe use drawings if that is better. Need to use the new logo (attached) and only list the following stores and phone numbers: Northeast - Greensburg, PA 800.555.0143; Mid-Atlantic Portsmouth, VA 888.555.0187; Gulf Coast - Houston Ship Channel - 281.555.0162; Louisiana - 225.555.0139

```html
<!DOCTYPE html>
<html lang="en">
<head>
<meta charset="utf-8">
<title>Northgate Rentals &amp; Supply – Rental Product Flyer</title>
<link href="https://fonts.googleapis.com/css2?family=Montserrat:wght@500;600&family=Oswald:wght@300;400;500;600&display=swap" rel="stylesheet">
<style>
  :root{
    --backdrop:#d6d4d6;
    --navy-top:#171b36;
    --navy-mid:#1a2244;
    --navy-low:#1f3868;
    --white:#ffffff;
    --logo-blue:#2f63c4;
    --logo-grey:#9a9ea8;
    --thumb-white:#f7f8fa;
  }
  *{box-sizing:border-box;margin:0;padding:0}
  html,body{width:1200px;height:600px;overflow:hidden}
  body{background:var(--backdrop);font-family:"Montserrat",sans-serif;color:var(--white);position:relative}

  .sheet{
    position:absolute;top:30px;width:382px;height:540px;
    background:linear-gradient(165deg,var(--navy-top) 0%,var(--navy-mid) 45%,var(--navy-low) 100%);
    box-shadow:6px 6px 10px rgba(0,0,0,.35);
  }
  .sheet--products{left:203px}
  .sheet--stores{left:615px}

  .brand{position:absolute;top:38px;left:0;width:100%;text-align:center}
  .brand__name{font-family:"Oswald",sans-serif;font-weight:600;font-size:30px;letter-spacing:1px;color:var(--logo-grey);text-transform:uppercase;line-height:1}
  .brand__tagline{margin-top:6px;font-size:6.5px;letter-spacing:.6px;color:var(--logo-blue);text-transform:uppercase}
  .sheet--stores .brand{top:34px}
  .sheet--stores .brand__name{font-size:24px}

  .sheet__title{position:absolute;top:118px;width:100%;text-align:center;font-family:"Oswald",sans-serif;font-weight:500;font-size:14.5px}
  .sheet__intro{position:absolute;top:163px;width:100%;text-align:center;font-family:"Oswald",sans-serif;font-weight:300;font-size:12.5px;line-height:15.5px}

  .catalog{position:absolute;left:19px;top:204px;width:345px;height:313px;border:2px solid var(--white);
    display:grid;grid-template-columns:repeat(3,94px);grid-template-rows:repeat(3,1fr);column-gap:9px;padding:10px 20px 16px 20px}
  .product{display:flex;flex-direction:column;align-items:center}
  .product__label{font-size:8px;font-weight:500;white-space:nowrap;height:13px;line-height:13px;text-transform:uppercase}
  .product__label--small{font-size:7px}
  .product__photo{width:94px;height:63px;background:var(--thumb-white);padding:8px}
  .product__photo span{display:block;width:100%;height:100%;border-radius:3px}
  .tone-grey span{background:radial-gradient(circle,#8d9096,#d4d6da)}
  .tone-blue span{background:radial-gradient(circle,#2d6fc4,#bcd2ee)}
  .tone-dark span{background:radial-gradient(circle,#2a2c33,#c8c9cc)}
  .tone-green span{background:radial-gradient(circle,#2f8a4a,#d6e4d6)}
  .tone-red span{background:radial-gradient(circle,#b42b2b,#d9d3d3)}
  .tone-olive span{background:radial-gradient(circle,#3f4a3a,#d3d7cf)}

  .region{position:absolute;left:13px;width:356px;border:2px solid var(--white)}
  .region--north{top:184px;height:88px}
  .region--south{top:316px;height:97px}
  .location{position:absolute;width:128px}
  .location__photo{width:128px;height:86px;border:3px solid var(--white)}
  .photo-city{background:linear-gradient(180deg,#a9b7c2 0%,#8a7c74 45%,#5e4f48 100%)}
  .photo-harbor{background:linear-gradient(180deg,#b7c3cb 0%,#6f7d86 40%,#3c5262 100%)}
  .photo-river{background:linear-gradient(180deg,#aabace 0%,#6b86a3 45%,#4d5f7a 100%)}
  .photo-channel{background:linear-gradient(180deg,#b6bec6 0%,#8f9498 45%,#536573 100%)}
  .location__line{display:flex;align-items:flex-start;gap:5px;font-size:6.5px;font-weight:500;margin-top:5px;line-height:8px;text-transform:uppercase}
  .location__line svg{flex:none}
  .location__line + .location__line{margin-top:4px}

  .headquarters{position:absolute;left:13px;top:420px;width:356px;height:111px;border:2px solid var(--white);text-align:center}
  .headquarters__title{margin-top:20px;font-family:"Oswald",sans-serif;font-weight:500;font-size:11.5px;letter-spacing:.3px}
  .headquarters__address{margin-top:8px;font-family:"Oswald",sans-serif;font-weight:400;font-size:9.5px;line-height:12px}
  .headquarters__web{display:flex;justify-content:center;align-items:center;gap:5px;margin-top:11px;font-family:"Oswald",sans-serif;font-weight:300;font-size:6.5px;line-height:8px;text-align:left;text-transform:uppercase}
</style>
</head>
<body>

<section class="sheet sheet--products" aria-label="Products for rent">
  <header class="brand">
    <div class="brand__name">Northgate</div>
    <div class="brand__tagline">Rentals &amp; Supply · Abrasive Blasting &amp; Coating Equipment</div>
  </header>
  <h1 class="sheet__title">Rent with Confidence!</h1>
  <p class="sheet__intro">Explore Our Wide Range of Quality<br>Products for Rent!</p>

  <div class="catalog">
    <div class="product"><div class="product__label">Dust Collectors</div><div class="product__photo tone-grey" role="img" aria-label="Photo of a trailer-mounted dust collector"><span></span></div></div>
    <div class="product"><div class="product__label">Decon Systems</div><div class="product__photo tone-blue" role="img" aria-label="Photo of a blue decontamination trailer"><span></span></div></div>
    <div class="product"><div class="product__label">Hand Tools</div><div class="product__photo tone-dark" role="img" aria-label="Photo of a pneumatic hand tool"><span></span></div></div>
    <div class="product"><div class="product__label product__label--small">Respiratory Systems</div><div class="product__photo tone-green" role="img" aria-label="Photo of a breathing air pump"><span></span></div></div>
    <div class="product"><div class="product__label">Air Management</div><div class="product__photo tone-red" role="img" aria-label="Photo of a trailer-mounted air heater"><span></span></div></div>
    <div class="product"><div class="product__label">Blasting Systems</div><div class="product__photo tone-blue" role="img" aria-label="Photo of a blue blast pot on a trailer"><span></span></div></div>
    <div class="product"><div class="product__label product__label--small">Air Drying Systems</div><div class="product__photo tone-blue" role="img" aria-label="Photo of an air drying cooler unit"><span></span></div></div>
    <div class="product"><div class="product__label product__label--small">Air &amp; Power Systems</div><div class="product__photo tone-olive" role="img" aria-label="Photo of a towable air compressor"><span></span></div></div>
    <div class="product"><div class="product__label product__label--small">High Volume Vacuums</div><div class="product__photo tone-blue" role="img" aria-label="Photo of a blue industrial vacuum unit"><span></span></div></div>
  </div>
</section>

<section class="sheet sheet--stores" aria-label="Stores and phone numbers">
  <header class="brand">
    <div class="brand__name">Northgate</div>
    <div class="brand__tagline">Rentals &amp; Supply · Abrasive Blasting &amp; Coating Equipment</div>
  </header>
  <h2 class="sheet__title">Our Stores and Phone Numbers</h2>

  <div class="region region--north"></div>
  <div class="region region--south"></div>

  <div class="location" style="left:52px;top:155px">
    <div class="location__photo photo-city" role="img" aria-label="Aerial photo of Greensburg, PA"></div>
    <div class="location__line"><svg width="7" height="8" viewBox="0 0 10 12"><path d="M5 11.5C2 8 1 6 1 4.5a4 4 0 0 1 8 0C9 6 8 8 5 11.5z" fill="none" stroke="#fff"/><circle cx="5" cy="4.5" r="1.4" fill="none" stroke="#fff"/></svg>Northeast - Greensburg, PA</div>
    <div class="location__line"><svg width="8" height="8" viewBox="0 0 12 12"><path d="M3 1l2 3-1.3 1.2a7 7 0 0 0 3.1 3.1L8 7l3 2-1 2C5 11 1 7 1 2z" fill="none" stroke="#fff"/></svg>800.555.0143</div>
  </div>
  <div class="location" style="left:203px;top:155px">
    <div class="location__photo photo-harbor" role="img" aria-label="Aerial photo of the Portsmouth, VA waterfront"></div>
    <div class="location__line"><svg width="7" height="8" viewBox="0 0 10 12"><path d="M5 11.5C2 8 1 6 1 4.5a4 4 0 0 1 8 0C9 6 8 8 5 11.5z" fill="none" stroke="#fff"/><circle cx="5" cy="4.5" r="1.4" fill="none" stroke="#fff"/></svg>Mid-Atlantic - Portsmouth, VA</div>
    <div class="location__line"><svg width="8" height="8" viewBox="0 0 12 12"><path d="M3 1l2 3-1.3 1.2a7 7 0 0 0 3.1 3.1L8 7l3 2-1 2C5 11 1 7 1 2z" fill="none" stroke="#fff"/></svg>888.555.0187</div>
  </div>
  <div class="location" style="left:52px;top:288px">
    <div class="location__photo photo-river" role="img" aria-label="Aerial photo of a Louisiana river bridge"></div>
    <div class="location__line"><svg width="7" height="8" viewBox="0 0 10 12"><path d="M5 11.5C2 8 1 6 1 4.5a4 4 0 0 1 8 0C9 6 8 8 5 11.5z" fill="none" stroke="#fff"/><circle cx="5" cy="4.5" r="1.4" fill="none" stroke="#fff"/></svg>Louisiana</div>
    <div class="location__line"><svg width="8" height="8" viewBox="0 0 12 12"><path d="M3 1l2 3-1.3 1.2a7 7 0 0 0 3.1 3.1L8 7l3 2-1 2C5 11 1 7 1 2z" fill="none" stroke="#fff"/></svg>225.555.0139</div>
  </div>
  <div class="location" style="left:203px;top:288px">
    <div class="location__photo photo-channel" role="img" aria-label="Aerial photo of the Houston Ship Channel refineries"></div>
    <div class="location__line"><svg width="7" height="8" viewBox="0 0 10 12"><path d="M5 11.5C2 8 1 6 1 4.5a4 4 0 0 1 8 0C9 6 8 8 5 11.5z" fill="none" stroke="#fff"/><circle cx="5" cy="4.5" r="1.4" fill="none" stroke="#fff"/></svg>Gulf Coast - Houston Ship<br>Channel</div>
    <div class="location__line"><svg width="8" height="8" viewBox="0 0 12 12"><path d="M3 1l2 3-1.3 1.2a7 7 0 0 0 3.1 3.1L8 7l3 2-1 2C5 11 1 7 1 2z" fill="none" stroke="#fff"/></svg>281.555.0162</div>
  </div>

  <div class="headquarters">
    <div class="headquarters__title">CORPORATE HEADQUARTERS:</div>
    <div class="headquarters__address">2210 FOUNDRY LANE • GREENSBURG, PA 15601<br>OFFICE: 800-555-0143 • FAX: 800-555-0178</div>
    <div class="headquarters__web">
      <svg width="15" height="15" viewBox="0 0 16 16" fill="none" stroke="#fff" stroke-width=".9"><circle cx="8" cy="8" r="7"/><ellipse cx="8" cy="8" rx="3" ry="7"/><path d="M1 8h14M2.2 4.3h11.6M2.2 11.7h11.6"/></svg>
      <span>www.northgaterentals.example<br>sales@northgaterentals.example</span>
    </div>
  </div>
</section>

</body>
</html>
```